Corvena Hotel, city center modern minimal hotel operating all year round, on Rhodes island Greece

city, modern ,all year operating hotel

Target Market(s)

tourists, business agents

Industry/Entity Type

tourism

Number of Pages Required

2 page

Requirements
Must have
• room type photos and descriptions, amenities individual listing (graphic), comments sections, map driving location details
Nice to have
• gallery section, modern and minimal design, amenities section, individual room type descriptions, photos and facilities

```html
<!DOCTYPE html>
<html lang="en">
<head>
<meta charset="utf-8">
<title>Corvena Hotel – Rhodes</title>
<link href="https://fonts.googleapis.com/css2?family=Libre+Baskerville:wght@400;700&family=Lato:wght@400;700&display=swap" rel="stylesheet">
<style>
:root{
  --gold:#c2993a;
  --green:#1f4a33;
  --green-deep:#1c4530;
  --sage:#6b8a72;
  --ink:#1b1b1b;
  --text:#3a3a3a;
  --grey:#e3e3e3;
  --pin:#d23a2f;
  --white:#ffffff;
}
*{box-sizing:border-box;margin:0;padding:0}
html,body{width:1200px;height:4605px;overflow:hidden}
body{font-family:'Lato',sans-serif;color:var(--text);background:var(--white);position:relative}
.serif{font-family:'Libre Baskerville',serif}
.abs{position:absolute}

/* top bar */
.topbar{position:absolute;top:0;left:0;width:1200px;height:34px;background:var(--gold);color:#fff;font-family:'Libre Baskerville',serif;font-size:14px}
.topbar span{position:absolute;top:9px;display:flex;align-items:center;gap:8px;white-space:nowrap}
.topbar svg{width:14px;height:14px}

/* nav */
.nav{position:absolute;top:34px;left:0;width:1200px;height:101px;background:#fff}
.brand{position:absolute;left:82px;top:34px;display:flex;align-items:center;gap:12px;font-family:'Libre Baskerville',serif;font-size:26px;color:var(--green);white-space:nowrap}
.brand i{display:block;width:28px;height:28px;background:var(--gold)}
.menu{position:absolute;top:30px;left:355px;display:flex}
.menu a{font-family:'Libre Baskerville',serif;font-size:12px;color:var(--green);text-decoration:none;text-align:center;letter-spacing:.5px;white-space:nowrap}
.menu a svg{display:block;margin:0 auto 6px;width:22px;height:22px}
.btn-gold{background:var(--gold);color:#fff;font-family:'Libre Baskerville',serif;font-weight:700;border-radius:20px;text-align:center;white-space:nowrap}
.book{position:absolute;left:970px;top:38px;width:126px;height:36px;line-height:36px;font-size:14px}

/* hero */
.hero-photo{position:absolute;top:135px;left:0;width:1200px;height:670px;background:linear-gradient(135deg,#3e4a33 0%,#6d7a55 30%,#8b7760 60%,#5b4a3b 100%)}
.diamond-back{position:absolute;left:418px;top:272px;width:400px;height:400px;background:var(--gold);transform:rotate(45deg);opacity:.9}
.diamond{position:absolute;left:417px;top:274px;width:372px;height:372px;background:var(--green);transform:rotate(45deg)}
.hero-text{position:absolute;left:403px;top:298px;width:400px;text-align:center;color:#fff}
.hero-text .kicker{font-family:'Libre Baskerville',serif;font-size:12px;font-weight:700}
.hero-text h1{font-family:'Libre Baskerville',serif;font-size:50px;line-height:58px;margin-top:22px;font-weight:700}
.hero-text .cta{display:inline-block;margin-top:28px;width:178px;height:46px;line-height:46px;font-size:12px}

/* booking */
.booking{position:absolute;left:93px;top:746px;width:1003px;height:364px;background:var(--sage);border-radius:20px}
.booking h2{text-align:center;color:#fff;font-family:'Libre Baskerville',serif;font-size:28px;padding-top:14px;font-weight:700}
.field{position:absolute;font-family:'Libre Baskerville',serif;font-size:11px;color:#fff;font-weight:700}
.field .box{margin-top:8px;height:36px;background:#fff;border-radius:6px;color:#777;font-family:'Lato',sans-serif;font-size:11px;line-height:36px;padding:0 10px;font-weight:700;position:relative}
.field .box.sel{color:#222}
.field .box.sel:after{content:'';position:absolute;right:10px;top:16px;border:4px solid transparent;border-top-color:#222}
.search{position:absolute;left:418px;top:273px;width:168px;height:54px;line-height:54px;font-size:22px;border-radius:28px}

/* headings */
.mark{display:block;width:26px;height:26px;background:var(--green);border:4px solid var(--gold)}
.h2{font-family:'Libre Baskerville',serif;color:var(--ink);font-size:30px;font-weight:700;letter-spacing:.5px;white-space:nowrap}
.about-copy{position:absolute;left:97px;top:1336px;width:463px}
.about-copy p{font-size:16px;line-height:30px;color:#333;text-align:justify}
.about-copy p + p{margin-top:30px}
.btn-green{position:absolute;background:var(--green);color:#fff;font-family:'Libre Baskerville',serif;font-weight:700;font-size:18px;text-align:center;border-radius:28px;box-shadow:0 4px 8px rgba(0,0,0,.3);white-space:nowrap}

/* about */
.about-feature{position:absolute;left:598px;top:1218px;width:576px;height:472px;display:flex;align-items:center;justify-content:center}
.about-feature .sq{width:300px;height:300px;background:var(--green);display:flex;align-items:center;justify-content:center;color:var(--gold);font-family:'Libre Baskerville',serif;font-size:30px;font-weight:700}

/* amenities */
.band{position:absolute;left:0;top:2112px;width:1200px;height:391px;background:var(--grey)}
.card{position:absolute;left:228px;top:1925px;width:742px;height:420px;background:#fff;box-shadow:0 4px 14px rgba(0,0,0,.25)}
.card-photo{position:absolute;left:18px;top:8px;width:706px;height:396px;background:linear-gradient(160deg,#2d2b24,#4a4131 50%,#243428)}
.amen{position:absolute;top:324px;color:#fff;font-family:'Libre Baskerville',serif;font-size:14px;font-weight:700;text-align:center;width:180px;white-space:nowrap}
.amen svg{display:block;margin:0 auto 6px}
.arrow{position:absolute;top:2128px;width:22px;height:22px;border-radius:50%;background:var(--green)}
.outline-btn{position:absolute;left:465px;top:2380px;width:270px;height:60px;border:2px solid var(--gold);border-radius:30px;text-align:center;line-height:56px;font-family:'Libre Baskerville',serif;font-size:19px;color:var(--ink);font-weight:700;white-space:nowrap}

/* rooms */
.room-photo{position:absolute;left:598px;top:2506px;width:602px;height:510px;background:linear-gradient(180deg,#4f5d6e 0%,#6b6556 45%,#b9b6ae 75%,#8e8a83 100%)}

/* gallery */
.gallery-bg{position:absolute;left:0;top:3016px;width:1200px;height:824px;background:var(--grey)}
.tile{position:absolute}

/* footer */
.footer{position:absolute;left:0;top:3840px;width:1200px;height:765px;background:var(--green-deep);color:#fff}
.footer .label{font-family:'Libre Baskerville',serif;font-size:17px}
.contact-row{position:absolute;left:98px;display:flex;gap:18px;align-items:flex-start;font-size:16px;line-height:26px}
.contact-row i{display:flex;align-items:center;justify-content:center;flex:none;width:34px;height:34px;border-radius:50%;background:#fff}
.map{position:absolute;left:465px;top:80px;width:641px;height:540px;border-radius:18px;background:linear-gradient(135deg,#f1f1f1,#dcdcdc);overflow:hidden}
.map .pin{position:absolute;left:274px;top:186px}
.foot-nav{position:absolute;left:98px;top:616px;width:1002px;border-top:1px dashed rgba(255,255,255,.6);padding-top:24px;display:flex;font-family:'Libre Baskerville',serif;font-size:13px;white-space:nowrap}
.foot-nav span{margin-right:14px}
.social{position:absolute;top:542px;width:40px;height:40px;border-radius:50%;background:#fff}
</style>
</head>
<body>

<div class="topbar">
  <span style="left:92px"><svg viewBox="0 0 16 16" fill="none" stroke="#fff" stroke-width="1.5"><rect x="1" y="3" width="14" height="10"/><path d="M1 3l7 6 7-6"/></svg>info@corvenahotel.gr</span>
  <span style="left:440px"><svg viewBox="0 0 16 16" fill="#fff"><path d="M8 1a5 5 0 0 0-5 5c0 4 5 9 5 9s5-5 5-9a5 5 0 0 0-5-5zm0 7a2 2 0 1 1 0-4 2 2 0 0 1 0 4z"/></svg>Odos Filellinon 12, Rhodes 851 00</span>
  <span style="left:926px"><svg viewBox="0 0 16 16" fill="#fff"><path d="M3 1l3 3-2 2a9 9 0 0 0 6 6l2-2 3 3-2 2C6 15 1 10 1 3z"/></svg>+30 2241055190</span>
</div>

<header class="nav">
  <div class="brand"><i></i>Corvena Hotel</div>
  <nav class="menu">
    <a style="width:60px" href="#"><svg viewBox="0 0 24 24" fill="none" stroke="#1f4a33" stroke-width="1.5"><path d="M3 11l9-8 9 8v10H3z"/></svg>HOME</a>
    <a style="width:120px" href="#"><svg viewBox="0 0 24 24" fill="none" stroke="#1f4a33" stroke-width="1.5"><rect x="3" y="9" width="18" height="8"/><path d="M3 17v3M21 17v3M6 9V6h12v3"/></svg>ROOMS</a>
    <a style="width:100px" href="#"><svg viewBox="0 0 24 24" fill="none" stroke="#1f4a33" stroke-width="1.5"><rect x="3" y="5" width="18" height="14"/><path d="M3 16l6-5 5 4 3-2 4 3"/></svg>GALLERY</a>
    <a style="width:124px" href="#"><svg viewBox="0 0 24 24" fill="none" stroke="#1f4a33" stroke-width="1.5"><rect x="3" y="6" width="18" height="12"/><path d="M3 6l9 7 9-7"/></svg>CONTACT</a>
    <a style="width:170px" href="#"><svg viewBox="0 0 24 24" fill="none" stroke="#1f4a33" stroke-width="1.5"><rect x="4" y="3" width="16" height="18"/><path d="M8 7h2M14 7h2M8 11h2M14 11h2M10 21v-4h4v4"/></svg>HOTEL WITH FLIGHT</a>
  </nav>
  <div class="btn-gold book">BOOK NOW</div>
</header>

<section>
  <div class="hero-photo" role="img" aria-label="Rooftop terrace with timber fence, wooden deck and green plants"></div>
  <div class="diamond-back"></div>
  <div class="diamond"></div>
  <div class="hero-text">
    <div class="kicker">INDOOR &amp; OUTDOOR</div>
    <h1>ENJOY<br>A LUXURY<br>EXPERIENCE</h1>
    <div class="btn-gold cta">ROOMS &amp; SUITES</div>
  </div>

  <form class="booking">
    <h2>CORVENA CITY HOTEL RHODES</h2>
    <div class="field" style="left:24px;top:100px;width:310px">FULL NAME*<div class="box">Corvena</div></div>
    <div class="field" style="left:349px;top:100px;width:310px">EMAIL*<div class="box">info@corvenahotel.com</div></div>
    <div class="field" style="left:667px;top:100px;width:310px">ARRIVAL DATE*<div class="box sel">21-10-2022</div></div>
    <div class="field" style="left:24px;top:178px;width:310px">DEPARTURE DATE*<div class="box sel">21-10-2022</div></div>
    <div class="field" style="left:349px;top:178px;width:310px">ROOMS*<div class="box sel">-- Single --</div></div>
    <div class="field" style="left:670px;top:178px;width:141px">ADULTS*<div class="box sel">-- 01--</div></div>
    <div class="field" style="left:836px;top:178px;width:141px">CHILDREN*<div class="box sel">-- 0--</div></div>
    <div class="btn-gold search">SEARCH</div>
  </form>
</section>

<section>
  <i class="mark abs" style="left:92px;top:1218px"></i>
  <h2 class="h2 abs" style="left:97px;top:1275px">ABOUT CORVENAHOTEL</h2>
  <div class="about-copy">
    <p>Situated at the very heart of Rhodes town, the hotel provides easy access to all major points of interest all within walking distance.</p>
    <p>The hotel is renowned in the local market due to its operation which “runs” 365 days a year. All rooms have been renovated recently and offer a unique design with modern furnishes. Being in constant operation for the last 47 years, and gone through numerous</p>
  </div>
  <div class="btn-green" style="left:93px;top:1631px;width:185px;height:53px;line-height:53px">READ MORE</div>
  <div class="about-feature"><div class="sq">Corvena</div></div>
</section>

<section>
  <i class="mark abs" style="left:587px;top:1776px"></i>
  <h2 class="h2 abs" style="left:0;width:1200px;top:1816px;text-align:center;line-height:42px">AMENITIES INDIVIDUAL<br>LISTING</h2>
  <div class="band"></div>
  <span class="arrow" style="left:183px"><svg viewBox="0 0 22 22" width="22" height="22"><path d="M13 6l-5 5 5 5" stroke="#fff" stroke-width="2" fill="none"/></svg></span>
  <span class="arrow" style="left:986px"><svg viewBox="0 0 22 22" width="22" height="22"><path d="M9 6l5 5-5 5" stroke="#fff" stroke-width="2" fill="none"/></svg></span>
  <div class="card">
    <div class="card-photo" role="img" aria-label="Dimly lit hotel bedroom with lattice screen, striped pillows and bedside lamps"></div>
    <div class="amen" style="left:29px">
      <svg width="30" height="24" viewBox="0 0 30 24" fill="none" stroke="#fff" stroke-width="1.6"><circle cx="20" cy="5" r="3"/><path d="M6 12l6-4 5 5M2 18c4-3 6 3 10 0s6 3 10 0 6 3 6 3M2 22c4-3 6 3 10 0s6 3 10 0"/></svg>SWIMMING POOL</div>
    <div class="amen" style="left:281px">
      <svg width="30" height="24" viewBox="0 0 30 24" fill="none" stroke="#fff" stroke-width="1.6"><circle cx="20" cy="5" r="3"/><path d="M6 12l6-4 5 5M2 18c4-3 6 3 10 0s6 3 10 0 6 3 6 3M2 22c4-3 6 3 10 0s6 3 10 0"/></svg>GYM &amp; YOGA</div>
    <div class="amen" style="left:528px">
      <svg width="30" height="24" viewBox="0 0 30 24" fill="none" stroke="#fff" stroke-width="1.6"><circle cx="20" cy="5" r="3"/><path d="M6 12l6-4 5 5M2 18c4-3 6 3 10 0s6 3 10 0 6 3 6 3M2 22c4-3 6 3 10 0s6 3 10 0"/></svg>SPA &amp; MASSAGE</div>
  </div>
  <div class="outline-btn">VIEW ALL AMENITIES</div>
</section>

<section>
  <i class="mark abs" style="left:92px;top:2584px"></i>
  <h2 class="h2 abs" style="left:90px;top:2628px">ROOMS</h2>
  <h3 class="abs serif" style="left:90px;top:2690px;font-size:36px;color:var(--green);font-weight:700;white-space:nowrap">SINGLE ROOM</h3>
  <p class="abs serif" style="left:90px;top:2762px;width:470px;font-size:15px;line-height:26px;color:var(--ink)">This comfortable room features a balcony, laminated floors, private bathroom with shower, office desk, satellite TV and other amenities.</p>
  <div class="btn-green" style="left:92px;top:2871px;width:185px;height:53px;line-height:53px">READ MORE</div>
  <div class="room-photo" role="img" aria-label="Rooftop terrace at dusk with white gazebo, sun loungers and white pebble bed"></div>
</section>

<section>
  <div class="gallery-bg"></div>
  <i class="mark abs" style="left:587px;top:3096px"></i>
  <h2 class="h2 abs" style="left:0;width:1200px;top:3145px;text-align:center">OUR GALLERY</h2>
  <div class="tile" style="left:111px;top:3248px;width:476px;height:227px;background:linear-gradient(135deg,#2b2a22,#3e3a2c)" role="img" aria-label="Dark hotel bedroom interior"></div>
  <div class="tile" style="left:600px;top:3248px;width:236px;height:227px;background:linear-gradient(180deg,#6b5a3c,#2a2620)" role="img" aria-label="Bedroom with striped bedding and leaf artwork"></div>
  <div class="tile" style="left:850px;top:3248px;width:237px;height:227px;background:linear-gradient(180deg,#6f8fa6,#9a6a4a 60%,#3c3028)" role="img" aria-label="Guest in red dress on terrace at sunset with lanterns"></div>
  <div class="tile" style="left:111px;top:3483px;width:232px;height:227px;background:linear-gradient(180deg,#d8cfc0,#8a7a66 60%,#3e3830)" role="img" aria-label="Reception desk with warm ceiling lights"></div>
  <div class="tile" style="left:356px;top:3483px;width:231px;height:227px;background:linear-gradient(160deg,#7a5648,#4a3a34)" role="img" aria-label="Hotel facade in stone and timber"></div>
  <div class="tile" style="left:602px;top:3483px;width:485px;height:227px;background:linear-gradient(160deg,#2d2b24,#4a4131 50%,#243428)" role="img" aria-label="Bedroom with lattice screen and striped pillows"></div>
</section>

<footer class="footer">
  <div class="abs label" style="left:98px;top:112px">GET IN TOUCH</div>
  <h2 class="abs serif" style="left:98px;top:170px;font-size:33px;line-height:47px;font-weight:400;white-space:nowrap">CONTACT US<br>TODAY</h2>
  <div class="contact-row" style="top:279px"><i><svg width="14" height="16" viewBox="0 0 16 16" fill="#1f4a33"><path d="M8 1a5 5 0 0 0-5 5c0 4 5 9 5 9s5-5 5-9a5 5 0 0 0-5-5zm0 7a2 2 0 1 1 0-4 2 2 0 0 1 0 4z"/></svg></i><span>Odos Filellinon 12, Rhodes<br>851 00</span></div>
  <div class="contact-row" style="top:379px"><i><svg width="16" height="14" viewBox="0 0 16 14" fill="none" stroke="#1f4a33" stroke-width="1.6"><rect x="1" y="2" width="14" height="10"/><path d="M1 2l7 6 7-6"/></svg></i><span style="line-height:34px">info@corvenahotel.gr</span></div>
  <div class="contact-row" style="top:445px"><i><svg width="14" height="14" viewBox="0 0 16 16" fill="#1f4a33"><path d="M3 1l3 3-2 2a9 9 0 0 0 6 6l2-2 3 3-2 2C6 15 1 10 1 3z"/></svg></i><span style="line-height:34px">(+30) 2241055190-2</span></div>
  <div class="abs serif" style="left:105px;top:510px;font-size:14px;white-space:nowrap">GET DIRECTIONS</div>
  <span class="social" style="left:107px"></span>
  <span class="social" style="left:167px"></span>
  <div class="map" role="img" aria-label="Street map of Rhodes town, pin on Odos Filellinon 12 in the Niohori district, a short drive south of Elli Beach">
    <svg class="pin" width="24" height="34" viewBox="0 0 24 34"><path d="M12 1C6 1 1 6 1 12c0 8 11 21 11 21s11-13 11-21C23 6 18 1 12 1z" fill="var(--pin)"/><circle cx="12" cy="12" r="4" fill="#fff"/></svg>
  </div>
  <div class="foot-nav"><span>HOME /</span><span>&nbsp;&nbsp;ROOMS /</span><span>&nbsp;&nbsp;GALLERY /</span><span>&nbsp;&nbsp;CONTACT /</span><span>&nbsp;&nbsp;HOTEL WITH FLIGHT</span></div>
  <div class="abs" style="left:988px;top:624px;display:flex;align-items:center;gap:8px;font-family:'Libre Baskerville',serif;font-size:14px;white-space:nowrap"><span style="display:block;width:38px;height:38px;border-radius:50%;background:var(--gold)"></span>Chat Here</div>
  <div class="abs serif" style="left:98px;top:692px;font-size:12px;white-space:nowrap">© COPYRIGHTS 2022 CORVENA CITY HOTEL | ALL RIGHTS RESERVED</div>
</footer>

</body>
</html>
```